5 website banners (slides show)

We need 5 website sliding banners created for a website all about internet safety. The topics for each banner are:

Cyberbullying
Fraud
seniors
social networking

Sizes: 953 pixels x 281 pixels

I have stock images to use or feel free to use your own or one I can purchase from pixelharbor.example.

Industry/Entity Type

Internet

```html
<!DOCTYPE html>
<html lang="en">
<head>
<meta charset="utf-8">
<title>SafeClicks – Coral Isle Online Safety and Security</title>
<link href="https://fonts.googleapis.com/css2?family=Ubuntu:wght@400;500;700&family=Great+Vibes&family=Arimo:wght@400&display=swap" rel="stylesheet">
<style>
  :root{
    --pink:#ec008c;
    --green:#7dbb2a;
    --green-light:#8ecb32;
    --green-nav-active:#8bc63a;
    --green-strip:#8cc83a;
    --purple:#8a1a8c;
    --text-grey:#8a9aa8;
    --white:#ffffff;
  }
  *{box-sizing:border-box;margin:0;padding:0}
  html,body{width:1200px;height:900px;overflow:hidden;background:var(--white);font-family:"Arimo",Arial,sans-serif}
  .page{position:relative;width:1200px;height:900px}

  .utility-bar{position:absolute;left:116px;top:5px;width:950px;height:33px;background:var(--pink);border-radius:6px 6px 0 0}
  .utility-links{position:absolute;left:15px;top:8px;display:flex;gap:26px;font-size:13px;color:var(--white)}
  .social-square{position:absolute;left:610px;top:4px;width:25px;height:25px;background:#3b5998;border-radius:3px}
  .search{position:absolute;left:640px;top:2px;width:306px;height:29px;background:var(--white);border:1px solid #e8eef4}
  .search span{position:absolute;left:11px;top:7px;font-size:13px;color:#9aaab8}
  .search-btn{position:absolute;right:2px;top:2px;width:26px;height:24px;background:var(--pink);border-radius:3px}

  .brand-dot{position:absolute;left:134px;top:54px;width:96px;height:104px;border-radius:50%;background:var(--pink)}
  .brand-name{position:absolute;left:245px;top:68px;font-family:"Ubuntu",sans-serif;font-weight:500;font-size:48px;color:var(--pink);line-height:1;letter-spacing:-1px;white-space:nowrap}
  .brand-tag{position:absolute;left:248px;top:124px;font-family:"Ubuntu",sans-serif;font-weight:500;font-size:12px;color:var(--green);white-space:nowrap;line-height:1}

  .report{position:absolute;left:710px;top:61px;width:356px;height:96px;background:var(--green-light);border-radius:3px}
  .report-inner{position:absolute;inset:5px;border:1px dashed rgba(255,255,255,.7)}
  .report-title{position:absolute;left:17px;top:13px;font-family:"Ubuntu",sans-serif;font-weight:500;font-size:21px;color:var(--white);white-space:nowrap;line-height:1}
  .report-click{position:absolute;left:185px;top:41px;font-family:"Ubuntu",sans-serif;font-size:13px;color:var(--white);line-height:1}
  .report-call{position:absolute;left:14px;top:58px;font-family:"Ubuntu",sans-serif;font-weight:700;font-size:23px;color:var(--white);white-space:nowrap;line-height:1}
  .report-badge{position:absolute;left:268px;top:4px;width:72px;height:86px;background:#5a8fc8;border-radius:8px 8px 36px 36px}

  .main-nav{position:absolute;left:116px;top:175px;width:950px;height:67px;background:var(--green-strip);border-radius:6px;overflow:hidden}
  .main-nav ul{list-style:none;display:flex;height:56px;background:var(--green)}
  .main-nav li{flex:0 0 auto;font-family:"Ubuntu",sans-serif;font-size:15px;color:var(--white);text-align:center;line-height:56px;white-space:nowrap;border-right:1px solid var(--green-light)}
  .main-nav li.active{background:var(--green-nav-active)}

  .hero{position:absolute;left:114px;top:250px;width:953px;height:281px;overflow:hidden;background:linear-gradient(135deg,#b0127f,var(--purple) 60%,#6f1477)}
  .hero-photo{position:absolute;left:0;top:0;width:100%;height:100%;background:linear-gradient(120deg,#d8e4ec,#b89278 45%,#5a3a2a);clip-path:polygon(0 0,494px 0,343px 281px,0 281px)}
  .hero-stripe{position:absolute;inset:0}
  .hero-tag{position:absolute;left:628px;top:50px;padding:2px 8px;background:rgba(80,10,80,.75);border-radius:6px;font-family:"Ubuntu",sans-serif;font-size:17px;color:var(--white)}
  .hero-line{position:absolute;font-family:"Great Vibes",cursive;color:var(--white)}
  .hero-think{left:586px;top:86px;font-size:40px}
  .hero-post{left:540px;top:158px;font-size:46px;color:#3a0a3e}
  .hero-or{left:685px;top:176px;font-size:24px;color:#3a0a3e}
  .hero-text{left:772px;top:158px;font-size:46px;color:#3a0a3e}

  .issues{position:absolute;left:116px;top:544px;width:220px;height:380px;background:var(--green-light);border-radius:10px}
  .issues-frame{position:absolute;left:10px;top:10px;width:200px;height:360px;border:1px dashed rgba(255,255,255,.8);border-radius:8px}
  .issues h2{position:absolute;left:21px;top:30px;font-family:"Ubuntu",sans-serif;font-weight:700;font-size:15px;color:var(--white)}
  .issues ul{position:absolute;left:26px;top:57px;list-style:none;font-size:12px;color:var(--white);line-height:25px}

  .welcome{position:absolute;left:346px;top:544px;width:716px;height:360px;box-shadow:3px 0 4px -2px #ccc}
  .welcome h1{position:absolute;left:20px;top:20px;font-family:"Ubuntu",sans-serif;font-weight:700;font-size:25px;color:var(--pink)}
  .edit{position:absolute;left:20px;top:57px;font-size:12px;color:#b080c8}
  .edit::before{content:"";display:inline-block;width:4px;height:4px;border-radius:50%;background:#aab;margin-right:10px;vertical-align:middle}
  .welcome-copy{position:absolute;left:20px;top:92px;width:676px;font-size:12px;line-height:17px;color:var(--text-grey)}
  .welcome-copy p{margin-bottom:17px}

  .audience{position:absolute;top:830px;font-family:"Ubuntu",sans-serif;font-weight:700;font-size:15px;color:var(--pink)}
  .audience-photo{position:absolute;top:851px;width:200px;height:60px}
</style>
</head>
<body>
<div class="page">

  <div class="utility-bar">
    <div class="utility-links"><span>Home</span><span>FAQs</span><span>Contact</span></div>
    <div class="social-square" aria-label="Social"></div>
    <div class="search"><span>Search...</span><div class="search-btn"></div></div>
  </div>

  <div class="brand-dot"></div>
  <div class="brand-name">SAFECLICKS</div>
  <div class="brand-tag">CORAL ISLE ONLINE SAFETY AND SECURITY</div>

  <div class="report">
    <div class="report-inner"></div>
    <div class="report-title">REPORT A CYBERCRIME</div>
    <div class="report-click">CLICK HERE</div>
    <div class="report-call">or call 1-555-010-2030</div>
    <div class="report-badge"></div>
  </div>

  <nav class="main-nav">
    <ul>
      <li class="active" style="width:80px">HOME</li>
      <li style="width:86px">ABOUT</li>
      <li style="width:135px">FOR PARENTS</li>
      <li style="width:117px">FOR TEENS</li>
      <li style="width:132px">FOR TWEENS</li>
      <li style="width:103px">FOR KIDS</li>
      <li style="width:145px">FOR TEACHERS</li>
      <li style="width:122px">RESOURCES</li>
    </ul>
  </nav>

  <section class="hero">
    <div class="hero-photo" role="img" aria-label="Photo of a smiling family gathered around a laptop"></div>
    <svg class="hero-stripe" width="953" height="281" viewBox="0 0 953 281">
      <line x1="494" y1="0" x2="343" y2="281" stroke="#ffffff" stroke-width="5"/>
      <line x1="502" y1="0" x2="351" y2="281" stroke="#a01890" stroke-width="6"/>
      <circle cx="880" cy="55" r="30" fill="#d85ac8" opacity=".35"/>
      <circle cx="680" cy="240" r="55" fill="#d85ac8" opacity=".25"/>
      <circle cx="470" cy="245" r="12" fill="#f0a0e0" opacity=".45"/>
    </svg>
    <div class="hero-tag">#Social Network</div>
    <div class="hero-line hero-think">Think before you</div>
    <div class="hero-line hero-post">Post</div>
    <div class="hero-line hero-or">or</div>
    <div class="hero-line hero-text">Text</div>
  </section>

  <aside class="issues">
    <div class="issues-frame"></div>
    <h2>CHOOSE AN ISSUE</h2>
    <ul>
      <li>Cyberbullying</li><li>Sexting</li><li>Internet Safety</li><li>Fraud</li>
      <li>Mobile Devices</li><li>Gangs</li><li>Blogging</li><li>Predators</li>
      <li>Copywriting</li><li>Social Networking</li><li>Gaming</li><li>eMailing, Chat Rooms</li>
    </ul>
  </aside>

  <main class="welcome">
    <h1>WELCOME</h1>
    <div class="edit">Edit</div>
    <div class="welcome-copy">
      <p>Welcome to SafeClicks, Coral Isle's source of information on internet safety, brought to you by the Ministry of Digital Affairs. Our aim is to provide practical tips, resources and contact information to help parents, children and educators to use the Internet safely and be on guard against online predators and other inappropriate online content.</p>
      <p>By knowing the dangers and how to avoid them, you can take advantage of all the positive aspects of the Internet while avoiding most of its pitfalls.</p>
      <p>The Ministry of Digital Affairs partners with the Harbour Police Service, Northwind Software, Pixel Pals and a number of other organizations locally and internationally to bring innovative and media rich educational tools to Coral Isle</p>
    </div>
  </main>

  <div class="audience" style="left:356px">KIDS</div>
  <div class="audience" style="left:591px">TWEENS</div>
  <div class="audience" style="left:826px">TEENS</div>
  <div class="audience-photo" style="left:356px;background:linear-gradient(#e8dcd0,#b89078)" role="img" aria-label="Photo of a young child"></div>
  <div class="audience-photo" style="left:591px;background:linear-gradient(#9a88b8,#5a3a30)" role="img" aria-label="Photo of a preteen girl"></div>
  <div class="audience-photo" style="left:826px;background:linear-gradient(#c8b8a8,#8a6a58)" role="img" aria-label="Photo of a group of teenagers"></div>

</div>
</body>
</html>
```